Companybrochure for Consulting & Financing Firm

I need to have a Company Brochure asap for our company. We have a website that describes what we do, but we need also a brochure, that can be sent by PDF of eventually be printed as well.

The brochure should be short but nice and appealing to the customers.

We provide professional management consulting and help our customers to get finance for very diferent projects. Our business has a lot to do with personal relations, but also we are very professional in the way we work and how develop the solutions for our clients. Our clients are mainly government-owned firm, but also private trading companies and wealthy private investors.

Our customers are mainly in Latin America, but the company is headquater is in Switzerland. We are opening offices in Panama and Caracas, this should be easaly be adabtable later.

Please have a look at our website www.vorelpartners.ch. In the brochure, we would segment our services in 1.) Project Developments 2.) Management Conulting 3.) Investment Management and 4.) Finance Solutions.

Also do have a look at www.vorelpartners.ch
(Click E for the English version)
Updates

I managed to put the Mock-Up to the Website.
It is actually not really a mock-up, it is a version I have designed myself.
Well as I am not a designer, I hope you can make it much better.
The content however is what I would put in any other design as well.

Target Market(s)

Top Management, Investors, Entrepreneurs, Government Officials

Industry/Entity Type

Management Consulting

Requirements
Must have
• Design should reflect this image elements:

We are entrepreneurs.
We are comitted to get things done.
We work closely with the client side by side.
We are a professional partner.
We are not afraid of delivering unconventional solutions.
We look at the problem from various angles.
We analyse, develop solutions and implent results.
Should not have
• Typical US-American style elements. We do not want to give the impression of being a US company.

We do not want to appear to be neo-liberal. We are a politically neutral professional consulting firm.

```html
<!DOCTYPE html>
<html lang="en">
<head>
<meta charset="utf-8">
<title>Vorel Partners – Services</title>
<link rel="stylesheet" href="https://fonts.googleapis.com/css2?family=Arimo:wght@400;700&family=PT+Sans:wght@400&display=swap">
<style>
  :root {
    --canvas: #c6c7c9;
    --panel: #d0d1d3;
    --title-band: #e3e4e6;
    --navy: #3b4880;
    --heading: #2f3b7a;
    --body: #4a4a4c;
    --accent-link: #2f3b7a;
  }
  * { margin: 0; padding: 0; box-sizing: border-box; }
  html, body {
    width: 1200px; height: 434px; overflow: hidden;
    background: var(--canvas);
    font-family: "Arimo", Arial, sans-serif;
  }
  .spread { position: relative; width: 1200px; height: 434px; }
  .service-card {
    position: absolute; top: 12px; width: 578px; height: 409px;
    background: var(--panel);
    overflow: hidden;
  }
  .service-card--consulting { left: 17px; }
  .service-card--investment { left: 605px; }
  .service-photo { display: block; width: 578px; height: 210px; }
  .service-rule { height: 14px; background: var(--navy); }
  .service-title {
    height: 40px; background: var(--title-band);
    padding-left: 51px; line-height: 40px;
    font-size: 21px; font-weight: 700; color: var(--heading);
  }
  .service-text {
    padding: 9px 0 0 51px;
    font-family: "PT Sans", "Myriad Pro", Arial, sans-serif;
    font-size: 10.6px; line-height: 13.4px; color: var(--body);
    white-space: nowrap;
  }
  .service-text p + p { margin-top: 13.4px; }
  .service-text .principle { color: var(--accent-link); }
</style>
</head>
<body>
<main class="spread">
  <section class="service-card service-card--consulting">
    <svg class="service-photo" role="img" aria-label="Photo of a consulting team seated around a glass meeting table in a bright office" viewBox="0 0 578 210">
      <defs>
        <linearGradient id="office-tones" x1="0" y1="0" x2="1" y2="1">
          <stop offset="0" stop-color="#d9dde2"/>
          <stop offset="0.5" stop-color="#a7adb6"/>
          <stop offset="1" stop-color="#5a606b"/>
        </linearGradient>
      </defs>
      <rect width="578" height="210" fill="url(#office-tones)"/>
    </svg>
    <div class="service-rule"></div>
    <h2 class="service-title">&gt;&gt; Management Consulting</h2>
    <div class="service-text">
      <p>We elaborate solutions together with our customers and business partners by assisting<br>
      owners and top management in structured decision making.<br>
      We work goal-oriented following the principle:<br>
      <span class="principle">&gt;Analysis &gt;&gt; Solutions &gt;&gt;&gt; Results.</span></p>
      <p>Our consulting team members do all have many years of experience from previous assignments<br>
      at leading international management consulting companies and are familiar with methodologies<br>
      used in management consulting. We complete the team of consultants with the appropriate subject<br>
      matter experts.</p>
    </div>
  </section>

  <section class="service-card service-card--investment">
    <svg class="service-photo" role="img" aria-label="Photo of two business people shaking hands seen from below against a bright sky" viewBox="0 0 578 210">
      <defs>
        <linearGradient id="sky-tones" x1="0" y1="0" x2="1" y2="0">
          <stop offset="0" stop-color="#7f9cc4"/>
          <stop offset="0.5" stop-color="#e6edf5"/>
          <stop offset="1" stop-color="#8ea8cc"/>
        </linearGradient>
      </defs>
      <rect width="578" height="210" fill="url(#sky-tones)"/>
    </svg>
    <div class="service-rule"></div>
    <h2 class="service-title">&gt;&gt; Investment Management</h2>
    <div class="service-text">
      <p>Vorel Partners has a clear business-like approach to investments. We only engage in those projects or<br>
      companies with which we have a strong relationship.</p>
      <p>That is why we are also willing to take an entrepreneurial risk in the companies we invest in. We participate<br>
      with our own capital and assume functions in the company's management.</p>
      <p>Vorel Partners currently holds shares in seven SMEs; four of these to 100%. Participation is on equal terms,<br>
      and two of of the companies we are minority shareholders.</p>
    </div>
  </section>
</main>
</body>
</html>
```